Upmarket Dessert Lounge needs a Business Card Design

We are an upmarket dessert lounge needing a business card to match our image.

We want something that is simple yet beautiful, feminine, classy, sophisticated and elegant. We want it to stand out and don't mind if it is bold.

The design should include our logo and colours of red or maroon with gold highlights. We don't mind if black is used.

Marlow & Quince

Target Market(s)

For those who like to indulge or treat themselves and give in to their temptations on good quality desserts.

Industry/Entity Type

Business

Requirements
Must have
• Must include our logo and our name

Marlow & Quince

M & Q

```html
<!DOCTYPE html>
<html lang="en">
<head>
<meta charset="utf-8">
<title>Marlow &amp; Quince — Business Card</title>
<link rel="stylesheet" href="https://fonts.googleapis.com/css2?family=Open+Sans:wght@400;600&display=swap">
<style>
  :root {
    --backdrop-top: #f6eef0;
    --backdrop-bottom: #e7d3d7;
    --maroon: #6a1e1f;
    --maroon-deep: #5a1819;
    --gold: #efc185;
    --cream: #f7eee4;
    --shadow: rgba(60, 20, 25, 0.35);
  }
  * { box-sizing: border-box; margin: 0; padding: 0; }
  html, body {
    width: 1200px;
    height: 951px;
    overflow: hidden;
  }
  body {
    background: radial-gradient(ellipse at 50% 40%, var(--backdrop-top) 0%, var(--backdrop-bottom) 100%);
    font-family: "Open Sans", sans-serif;
    position: relative;
  }
  .card {
    position: absolute;
    width: 640px;
    height: 366px;
    border-radius: 22px;
    background: linear-gradient(160deg, var(--maroon) 0%, var(--maroon-deep) 100%);
    box-shadow: 0 18px 34px var(--shadow);
  }
  .card--front { left: 90px; top: 70px; }
  .card--back { left: 470px; top: 500px; }

  .front-mark {
    position: absolute;
    left: 0; right: 0;
    top: 130px;
    text-align: center;
    color: var(--gold);
    font-size: 40px;
    font-weight: 400;
    letter-spacing: 3px;
    text-transform: uppercase;
  }
  .front-url {
    position: absolute;
    left: 0; right: 0;
    top: 268px;
    text-align: center;
    color: var(--cream);
    font-size: 19px;
    letter-spacing: 2px;
  }

  .back-mark {
    position: absolute;
    left: 58px;
    top: 118px;
    width: 200px;
    text-align: center;
    color: var(--gold);
    font-size: 64px;
    font-weight: 400;
    line-height: 1;
    white-space: nowrap;
  }
  .back-details {
    position: absolute;
    right: 40px;
    top: 98px;
    text-align: right;
    color: var(--cream);
    font-size: 17px;
    line-height: 1.3;
  }
  .back-name {
    color: var(--gold);
    font-size: 23px;
    margin-bottom: 16px;
  }
  .back-address { margin-bottom: 22px; }
  .back-email .domain { color: var(--gold); }
</style>
</head>
<body>
  <section class="card card--front" aria-label="Card front">
    <p class="front-mark">Marlow &amp; Quince</p>
    <p class="front-url">www.marlowquince.com</p>
  </section>

  <section class="card card--back" aria-label="Card back">
    <p class="back-mark">M &amp; Q</p>
    <div class="back-details">
      <p class="back-name">Marlow &amp; Quince</p>
      <p class="back-address">48 Harbor Lane, Suite 210<br>Portland, Maine 04101</p>
      <p class="back-phone">207-555-0148</p>
      <p class="back-email">hello@<span class="domain">marlowquince</span>.com</p>
    </div>
  </section>
</body>
</html>
```